Website for courses for men for making money, health, fitness

I require a website which is going to be a mix of a crypto currency website and website aimed at providing men with money making, health, relationship advice courses and content

The name isn't decided yet so for now please call it something like

KESTREL YARD

A platform dedicated to making men wealthy, physically strong, mentally tough & successful with women

In the top right, I need it to show how many points they have, they must buy points in order to use them to claim the courses.

WHAT WE DO

Kestrel yard is a platform where you can learn everything you need about business, making money, crypto currency, fitness, health, mental toughness and resilience and how to be successful with women all in one place

HOW WILL THIS WORK & WHY SHOULD I BUY POINTS?

xxxxxxxxxxxxxxxxxxxxxxxx
xxxxxxxxxxxxxxxxxxxxxxx
xxxxxxxxxxxxxxxxxxxxx

AFFILIATE SCHEME

EARN UP TO $125 DOLLARS PER PERSON WHO SIGNS UP THROUGH YOUR LINK

START EARNING NOW - button
______________________________________________________

BUY POINTS
(A maximum of only $250 worth of points can be purchased per person until the platform goes fully live)

ROAD MAP & THE MODEL

2023

Q1 - PRE BUY IN FOR POINTS

Q2 - FULL WEBSITE LAUNCH

Q3 - APP LAUNCH

Q4 - IN APP ADVERT LAUNCH

It must have a very slick and sharp eye catching look, and be designed to convert people into purchasing points

some ideas of the feel of the website -

https://brivaloo.io/
https://nestorly.style/
https://plumwick.trelvanta.com/

```html
<!DOCTYPE html>
<html lang="en">
<head>
<meta charset="utf-8">
<title>Kestrel Yard</title>
<link rel="stylesheet" href="https://fonts.googleapis.com/css2?family=Roboto:wght@400;500;700;900&display=swap">
<style>
:root{
  --blue:#00b4f7;
  --blue-soft:#e6f5fd;
  --navy:#232f45;
  --ink:#2b2b2b;
  --grey:#666;
  --paper:#f4f4f4;
  --white:#fff;
  --q1:#9c1b47;
  --q2:#f5a623;
  --q3:#1fc0cb;
  --q4:#0f4b7c;
}
*{margin:0;padding:0;box-sizing:border-box}
html,body{width:1200px;height:3552px;overflow:hidden;background:var(--white)}
body{font-family:'Roboto',Arial,sans-serif;color:var(--ink)}
.page{position:relative;width:1200px;height:3552px;overflow:hidden}
.abs{position:absolute}
.bands{position:absolute;left:0;top:0}
.center{left:0;width:1200px;text-align:center}

.hero-photo{left:0;top:0;width:1200px;height:740px;
  background:linear-gradient(100deg,#6f6a66 0%,#8d8782 35%,#c9c3bb 55%,#5a4a40 80%,#3d3029 100%)}
.hero-shade{left:0;top:0;width:1200px;height:740px;background:linear-gradient(90deg,rgba(20,20,30,.55),rgba(20,20,30,.1) 60%)}

.logo{left:110px;top:28px;font-size:28px;font-weight:700;color:var(--white);letter-spacing:.2px}
.nav{left:457px;top:36px;display:flex;gap:26px}
.nav a{color:var(--white);font-size:13.5px;font-weight:700;text-decoration:none;padding-bottom:4px}
.nav a.active{border-bottom:2px solid var(--white)}
.btn-pill{top:23px;height:45px;border-radius:23px;display:flex;align-items:center;justify-content:center;gap:7px;font-size:14px;font-weight:700}
.btn-signup{left:852px;width:116px;background:var(--blue);color:var(--white)}
.btn-login{left:975px;width:115px;background:var(--white);color:var(--ink)}

.hero-title{left:110px;top:246px;font-size:52px;font-weight:700;color:var(--white)}
.hero-text{left:110px;top:322px;width:500px;font-size:14px;line-height:26px;color:var(--white)}
.scroll-cue{left:572px;top:613px;width:56px;height:56px;border-radius:50%;background:var(--white);border:3px solid var(--blue);display:flex;align-items:center;justify-content:center}

.section-title{font-size:50px;font-weight:700;line-height:1.05}
.on-blue{color:var(--white)}
.dark{color:var(--navy)}
.wwd-title{top:764px}
.wwd-text{left:300px;width:600px;top:838px;font-size:14px;line-height:26px;color:var(--white);text-align:center}

.how-title{top:1115px;font-size:42px;line-height:52px;color:var(--ink)}
.feature{top:1262px;width:220px;text-align:center}
.feature .ring{width:140px;height:140px;margin:0 auto;border-radius:50%;border:2px dotted #444;display:flex;align-items:center;justify-content:center}
.feature .disc{width:120px;height:120px;border-radius:50%;background:var(--blue-soft);border:3px solid var(--blue);display:flex;align-items:center;justify-content:center}
.feature h3{margin-top:17px;font-size:21px;font-weight:500;color:var(--ink)}
.feature p{margin-top:12px;font-size:14px;line-height:26px;color:var(--grey)}

.aff-title{top:1763px}
.aff-sub{top:1845px;font-size:21px;line-height:34px;font-weight:700;color:var(--navy)}
.btn-earn{left:481px;top:1929px;width:236px;height:51px;border-radius:26px;background:var(--navy);color:var(--white);font-size:13.5px;font-weight:700;display:flex;align-items:center;justify-content:center}

.buy-title{top:2160px}
.buy-note{top:2231px;font-size:14px;color:var(--grey)}
.stat{top:2275px;width:247px;height:193px;background:var(--blue-soft);text-align:center;padding-top:18px}
.stat .num{margin-top:4px;font-size:38px;font-weight:700;color:var(--navy);line-height:44px}
.stat .lbl{margin-top:6px;font-size:21px;color:var(--grey)}

.road-title{top:2658px}
.road-art{left:190px;top:2744px;width:820px;height:420px;border-radius:40px;
  background:radial-gradient(ellipse at 50% 40%,#e4e4e4 0%,#ececec 40%,rgba(244,244,244,0) 72%),linear-gradient(180deg,rgba(244,244,244,0),#8a8a8a 90%)}
.road-core{left:430px;top:2744px;width:390px;height:420px;
  background:radial-gradient(ellipse at 50% 100%,#4a4a4a 0%,#606060 45%,rgba(96,96,96,0) 72%)}
.bubble{color:var(--white);border-radius:46px;display:flex;align-items:center;gap:14px;padding:0 22px;box-shadow:0 10px 14px rgba(0,0,0,.18)}
.bubble .q{font-size:20px;font-weight:700;line-height:24px}
.bubble .t{font-size:13.5px;font-weight:700;line-height:26px}
.bubble .ico{width:46px;height:46px;flex:none}
.q1{left:190px;top:3006px;width:242px;height:104px;background:var(--q1)}
.q2{left:292px;top:2886px;width:215px;height:93px;background:var(--q2)}
.q3{left:713px;top:2834px;width:205px;height:87px;background:var(--q3);justify-content:space-between}
.q4{left:783px;top:2947px;width:224px;height:94px;background:var(--q4);justify-content:space-between}
.year{left:470px;top:3030px;width:315px;text-align:center;font-size:116px;font-weight:900;color:var(--white);letter-spacing:-2px;-webkit-text-stroke:3px #3a3a3a}

.foot-title{top:3290px;font-size:50px;font-weight:700;color:var(--white)}
.foot-nav{left:0;width:1200px;top:3360px;display:flex;justify-content:center;gap:26px}
.foot-nav a{color:var(--white);font-size:13.5px;font-weight:700;text-decoration:none}
.copy{top:3413px;font-size:13.5px;color:var(--white)}
.social{left:0;width:1200px;top:3449px;display:flex;justify-content:center;gap:5px}
.social span{width:30px;height:30px;border-radius:50%;background:var(--white);display:block}
</style>
</head>
<body>
<div class="page">

  <div class="abs hero-photo" role="img" aria-label="Photo of a smiling businesswoman with folded arms in a bright office meeting room"></div>
  <div class="abs hero-shade"></div>

  <svg class="bands" width="1200" height="3552" viewBox="0 0 1200 3552" aria-hidden="true">
    <path d="M0 728 Q600 554 1200 728 L1200 1103 Q600 937 0 1103 Z" fill="var(--blue)"/>
    <defs>
      <linearGradient id="affGrad" x1="0" y1="0" x2="1" y2="1">
        <stop offset="0" stop-color="#0aa6e8"/><stop offset=".5" stop-color="#00b9fa"/><stop offset="1" stop-color="#0aa3e4"/>
      </linearGradient>
    </defs>
    <path d="M0 1583 Q600 1755 1200 1583 L1200 2147 Q600 1977 0 2147 Z" fill="url(#affGrad)"/>
    <rect x="0" y="2570" width="1200" height="982" fill="var(--paper)"/>
  </svg>

  <!-- Header -->
  <div class="abs logo">KESTREL YARD</div>
  <nav class="abs nav">
    <a class="active" href="#">Home</a><a href="#">About Us</a><a href="#">Services</a><a href="#">Blog</a><a href="#">Contact us</a>
  </nav>
  <div class="abs btn-pill btn-signup">
    <svg width="11" height="13" viewBox="0 0 11 13"><circle cx="5.5" cy="3.3" r="3" fill="#fff"/><path d="M0 13c0-4 2.5-5.5 5.5-5.5S11 9 11 13z" fill="#fff"/></svg>Signup
  </div>
  <div class="abs btn-pill btn-login">
    <svg width="11" height="13" viewBox="0 0 11 13"><circle cx="5.5" cy="3.3" r="3" fill="#2b2b2b"/><path d="M0 13c0-4 2.5-5.5 5.5-5.5S11 9 11 13z" fill="#2b2b2b"/></svg>Log In
  </div>

  <h1 class="abs hero-title">KESTREL YARD</h1>
  <p class="abs hero-text">A platform dedicated to making men wealthy, physically strong, mentally tough &amp; successful with women In the top right, I need it to show how many points they have, they must buy points in order to use them to claim the courses.</p>

  <div class="abs scroll-cue">
    <svg width="22" height="26" viewBox="0 0 22 26"><path d="M11 2v21M3 15l8 8 8-8" fill="none" stroke="#111" stroke-width="2.6" stroke-linecap="round" stroke-linejoin="round"/></svg>
  </div>

  <!-- What we do -->
  <h2 class="abs center section-title on-blue wwd-title">WHAT WE DO</h2>
  <p class="abs wwd-text">Kestrel yard is a platform where you can learn everything you need about business, making money, crypto currency, fitness, health, mental toughness and resilience and how to be successful with women all in one place</p>

  <!-- How it works -->
  <h2 class="abs center section-title how-title">HOW WILL THIS WORK &amp;<br>WHY SHOULD I BUY POINTS?</h2>

  <div class="abs feature" style="left:123px">
    <div class="ring"><div class="disc">
      <svg width="62" height="62" viewBox="0 0 62 62" fill="none" stroke="#00b4f7" stroke-width="2.4" stroke-linejoin="round"><rect x="10" y="20" width="42" height="32" rx="6"/><circle cx="31" cy="17" r="9"/><path d="M22 44v-8M31 44V30M40 44v-10"/></svg>
    </div></div>
    <h3>Nemo enim ipsam</h3>
    <p>Lorem ipsum dolor sit amet, consectetur adipiscing elit, sed do eiusmod tempor</p>
  </div>
  <div class="abs feature" style="left:367px">
    <div class="ring"><div class="disc">
      <svg width="62" height="62" viewBox="0 0 62 62" fill="none" stroke="#00b4f7" stroke-width="2.4" stroke-linecap="round"><circle cx="21" cy="20" r="11"/><circle cx="41" cy="42" r="11"/><path d="M34 12c6 0 12 4 13 10M45 19l2 3 3-2M28 50c-6 0-12-4-13-10M17 43l-2-3-3 2"/><path d="M41 36v12M45 38h-5a2 2 0 0 0 0 4h2a2 2 0 0 1 0 4h-5"/></svg>
    </div></div>
    <h3>Nemo enim ipsam</h3>
    <p>Lorem ipsum dolor sit amet, consectetur adipiscing elit, sed do eiusmod tempor</p>
  </div>
  <div class="abs feature" style="left:611px">
    <div class="ring"><div class="disc">
      <svg width="62" height="62" viewBox="0 0 62 62" fill="none" stroke="#00b4f7" stroke-width="2.4" stroke-linecap="round" stroke-linejoin="round"><circle cx="33" cy="19" r="11"/><path d="M33 12v14M37 15h-5a2 2 0 0 0 0 4h2a2 2 0 0 1 0 4h-5"/><path d="M8 40h9l10 3h9a3 3 0 0 1 0 6H26M17 52l14 2 20-10a3 3 0 0 0-3-5l-12 5"/></svg>
    </div></div>
    <h3>Nemo enim ipsam</h3>
    <p>Lorem ipsum dolor sit amet, consectetur adipiscing elit, sed do eiusmod tempor</p>
  </div>
  <div class="abs feature" style="left:855px">
    <div class="ring"><div class="disc">
      <svg width="62" height="62" viewBox="0 0 62 62" fill="none" stroke="#00b4f7" stroke-width="2.4" stroke-linecap="round" stroke-linejoin="round"><path d="M31 44C18 35 14 29 14 23a8 8 0 0 1 17-3 8 8 0 0 1 17 3c0 6-4 12-17 21z"/><path d="M19 28h6l3-5 4 9 3-4h7"/><circle cx="46" cy="14" r="6"/><path d="M46 11v6M43 14h6M8 44h8l8 4h8"/></svg>
    </div></div>
    <h3>Nemo enim ipsam</h3>
    <p>Lorem ipsum dolor sit amet, consectetur adipiscing elit, sed do eiusmod tempor</p>
  </div>

  <!-- Affiliate -->
  <h2 class="abs center section-title on-blue aff-title">AFFILIATE SCHEME</h2>
  <p class="abs center aff-sub">EARN UP TO $125 DOLLARS PER PERSON WHO<br>SIGNS UP THROUGH YOUR LINK</p>
  <a class="abs btn-earn">START EARNING NOW</a>

  <!-- Buy points -->
  <h2 class="abs center section-title dark buy-title">BUY POINTS</h2>
  <p class="abs center buy-note">(A maximum of only $250 worth of points can be purchased per person until the platform goes fully live)</p>

  <div class="abs stat" style="left:210px">
    <svg width="66" height="66" viewBox="0 0 66 66" fill="none" stroke="#00b4f7" stroke-width="2.2" stroke-linejoin="round"><path d="M20 6l3 6 7 1-5 5 1 7-6-3-6 3 1-7-5-5 7-1z"/><path d="M44 10l2 4 5 1-4 3 1 5-4-3-4 3 1-5-4-3 5-1z"/><path d="M34 28l3 6 7 1-5 5 1 7-6-3-6 3 1-7-5-5 7-1z"/><path d="M8 54h10l10 4h14l16-10"/></svg>
    <div class="num">1829</div><div class="lbl">Points</div>
  </div>
  <div class="abs stat" style="left:478px">
    <svg width="66" height="66" viewBox="0 0 66 66" fill="none" stroke="#00b4f7" stroke-width="2.2" stroke-linejoin="round"><rect x="8" y="44" width="14" height="16"/><rect x="22" y="36" width="14" height="24"/><rect x="36" y="48" width="14" height="12"/><circle cx="26" cy="10" r="4"/><path d="M26 14v12l-5 8M26 20l-6 4M26 20l8-2M40 24l16-16M48 8h8v8"/></svg>
    <div class="num">325</div><div class="lbl">My Level</div>
  </div>
  <div class="abs stat" style="left:746px">
    <svg width="66" height="66" viewBox="0 0 66 66" fill="none" stroke="#00b4f7" stroke-width="2.2" stroke-linejoin="round"><path d="M6 60h56"/><rect x="10" y="42" width="9" height="18"/><rect x="24" y="34" width="9" height="26"/><rect x="38" y="26" width="9" height="34"/><rect x="52" y="18" width="9" height="42"/><path d="M14 28l2 3 4 1-3 3 1 4-4-2-4 2 1-4-3-3 4-1zM42 10l2 3 4 1-3 3 1 4-4-2-4 2 1-4-3-3 4-1z"/></svg>
    <div class="num">#1</div><div class="lbl">My Rank</div>
  </div>

  <!-- Road map -->
  <h2 class="abs center section-title dark road-title">ROAD MAP &amp; THE MODEL</h2>
  <div class="abs road-art" role="img" aria-label="Illustration of a road leading to a target with an arrow, over a faint world map"></div>
  <div class="abs road-core" aria-hidden="true"></div>

  <svg class="bands" width="1200" height="3552" viewBox="0 0 1200 3552" aria-hidden="true">
    <path d="M0 3110 Q600 3288 1200 3110 L1200 3552 L0 3552 Z" fill="var(--navy)"/>
  </svg>

  <div class="abs year">2023</div>

  <div class="abs bubble q1">
    <svg class="ico" viewBox="0 0 46 46"><circle cx="23" cy="23" r="22" fill="#fff"/><circle cx="23" cy="23" r="9" fill="none" stroke="#9c1b47" stroke-width="5"/></svg>
    <div><div class="q">Q1</div><div class="t">PRE BUY IN FOR<br>POINTS</div></div>
  </div>
  <div class="abs bubble q2">
    <svg class="ico" viewBox="0 0 46 46" fill="#fff"><path d="M23 8l18 8-18 8-18-8z"/><path d="M5 23l18 8 18-8v4l-18 8-18-8z"/><path d="M5 31l18 8 18-8v4l-18 8-18-8z"/></svg>
    <div><div class="q">Q2</div><div class="t">FULL WEBSITE<br>LAUNCH</div></div>
  </div>
  <div class="abs bubble q3">
    <div><div class="q">Q3</div><div class="t">APP LAUNCH</div></div>
    <svg class="ico" viewBox="0 0 46 46"><circle cx="23" cy="25" r="17" fill="#fff"/><path d="M23 15v10l7 5" fill="none" stroke="#1fc0cb" stroke-width="3" stroke-linecap="round"/><circle cx="9" cy="8" r="5" fill="#fff"/><circle cx="37" cy="8" r="5" fill="#fff"/></svg>
  </div>
  <div class="abs bubble q4">
    <div><div class="q">Q4</div><div class="t">IN APP ADVERT<br>LAUNCH</div></div>
    <svg class="ico" viewBox="0 0 46 46" fill="none" stroke="#fff" stroke-width="2.4"><path d="M8 14h24a4 4 0 0 1 4 4v10a4 4 0 0 1-4 4H18l-8 6v-6H8a4 4 0 0 1-4-4V18a4 4 0 0 1 4-4z"/><path d="M36 20h4a3 3 0 0 1 3 3v8l-3 5v-4"/></svg>
  </div>

  <!-- Footer -->
  <div class="abs center foot-title">KESTREL YARD</div>
  <nav class="abs foot-nav">
    <a href="#">Home</a><a href="#">About Us</a><a href="#">Services</a><a href="#">Blog</a><a href="#">Contact us</a>
  </nav>
  <p class="abs center copy">© Copyright 2022 Company name | All Rights Reserved</p>
  <div class="abs social" aria-label="Social links"><span></span><span></span><span></span><span></span></div>

</div>
</body>
</html>
```